Simple Business Card Design for Tavlo

Job:

Make a very simple, minimalist business card design with my details including adjusted logo. One side to be white (with logo & text). Other side to be yellow - try plain or with logo (or part of logo eg Z). Need business card to have continuity with website.

Logo:
Our logo is made from a free download font website:
http://www.typewell.net/search.php?q=rubber
but the spacing/kerning needs correcting/adjusting as the font spaces unevenly between letters (see attached files). Need logo to be very crisp/sharp when printed.

Printing:
We will be using Plika.com so the design needs to conform to their requirements, see here:

http://uk.plika.com/products/luxe/business-cards.html (scroll down for dimensions and guidelines)

Design:

must say "plant-based food consulting" underneath logo or somewhere
no address needed in contact section
sharp corners (not rounded)
one side white, one side yellow

name: Rosalind Whitcombe
1xmobile number: +44 7700900463
1xtwiiter: @brimcounsel
website address www.orchardtable.com
email address brim@orchardtable.com

Should be easy quick job, prompt + detailed feedback given, am online in UK 9am-10pm for next 3 days. Website is www.orchardtable.com

Industry/Entity Type

Business

Requirements
Must have
• The logo must be corrected. The kerning is not right.

Please use a warm-grey for text

Please submit in matt format, we will be printing matt finish.

Should not have
• Avoid using banners or curvy highlights

Please avoid using black

Please avoid submitting in gloss finish

```html
<!DOCTYPE html>
<html lang="en">
<head>
<meta charset="utf-8">
<title>Brim – Business Card</title>
<link rel="stylesheet" href="https://fonts.googleapis.com/css2?family=Mulish:wght@400;600;700&display=swap">
<style>
  :root {
    --backdrop: #5b5a58;
    --card-white: #f6f6f4;
    --brand-yellow: #ecd62a;
    --yellow-face: #f0d92c;
    --warm-grey: #5e5a55;
    --rule-grey: #d6d4d0;
    --white: #ffffff;
  }
  * { margin: 0; padding: 0; box-sizing: border-box; }
  html, body {
    width: 1200px; height: 1000px; overflow: hidden;
    background: var(--backdrop);
    font-family: "Mulish", Arial, sans-serif;
  }
  .canvas { position: relative; width: 1200px; height: 1000px; }
  .card {
    position: absolute; top: 359px; width: 425px; height: 279px;
    box-shadow: 3px 4px 8px rgba(0,0,0,0.35);
  }
  .card--front { left: 131px; background: var(--card-white); }
  .card--back { left: 651px; background: var(--yellow-face); }

  .wordmark {
    position: absolute; font-weight: 600; line-height: 1;
    letter-spacing: 3px; font-size: 52px;
  }
  .card--front .wordmark { left: 38px; top: 78px; color: var(--brand-yellow); }
  .card--back .wordmark { left: 0; right: 0; top: 118px; text-align: center; color: var(--white); font-size: 50px; }

  .tagline {
    position: absolute; right: 253px; top: 170px;
    text-align: right; font-size: 11px; line-height: 14px;
    color: var(--warm-grey); text-transform: uppercase; letter-spacing: 0.2px;
  }
  .divider {
    position: absolute; left: 200px; top: 80px; width: 1px; height: 142px;
    background: var(--rule-grey);
  }
  .holder-name {
    position: absolute; left: 229px; top: 80px;
    font-size: 15px; font-weight: 700; color: var(--warm-grey); letter-spacing: 0.3px;
  }
  .contact-list {
    position: absolute; left: 229px; top: 119px; list-style: none;
  }
  .contact-list li {
    display: flex; align-items: center; gap: 6px;
    height: 15.8px; font-size: 11px; color: var(--warm-grey);
  }
  .contact-icon { width: 10px; height: 10px; flex: none; }
</style>
</head>
<body>
<main class="canvas">
  <section class="card card--front" aria-label="Card front">
    <div class="wordmark">BRIM</div>
    <p class="tagline">Plant-based<br>food consulting</p>
    <div class="divider"></div>
    <h1 class="holder-name">ROSALIND WHITCOMBE</h1>
    <ul class="contact-list">
      <li>
        <svg class="contact-icon" viewBox="0 0 10 10"><circle cx="5" cy="5" r="4.5" fill="none" stroke="#ecd62a"/><path d="M3.3 2.8c.3 1.9 1.6 3.4 3.6 4l.5-.9-1-.6-.5.5c-.8-.4-1.4-1-1.7-1.8l.5-.4-.5-1z" fill="#ecd62a"/></svg>
        +44 7700900463
      </li>
      <li>
        <svg class="contact-icon" viewBox="0 0 10 10"><circle cx="5" cy="5" r="4.5" fill="#ecd62a"/></svg>
        @brimcounsel
      </li>
      <li>
        <svg class="contact-icon" viewBox="0 0 10 10"><circle cx="5" cy="5" r="4.5" fill="#ecd62a"/></svg>
        brimcounsel
      </li>
      <li>
        <svg class="contact-icon" viewBox="0 0 10 10"><circle cx="5" cy="5" r="4.5" fill="#ecd62a"/><rect x="2.6" y="3.4" width="4.8" height="3.4" fill="none" stroke="#fff" stroke-width="0.7"/><path d="M2.6 3.4L5 5.3 7.4 3.4" fill="none" stroke="#fff" stroke-width="0.7"/></svg>
        brim@orchardtable.com
      </li>
      <li>
        <svg class="contact-icon" viewBox="0 0 10 10"><circle cx="5" cy="5" r="4.3" fill="none" stroke="#ecd62a" stroke-width="0.9"/><ellipse cx="5" cy="5" rx="1.8" ry="4.3" fill="none" stroke="#ecd62a" stroke-width="0.7"/><path d="M0.8 5h8.4" stroke="#ecd62a" stroke-width="0.7"/></svg>
        www.orchardtable.com
      </li>
    </ul>
  </section>

  <section class="card card--back" aria-label="Card back">
    <div class="wordmark">BRIM</div>
  </section>
</main>
</body>
</html>
```